Construction Company

Design a clutter free business card, it can be double-sided utilizing the logo for VKM Ltd simple with all relevant contact information.

Please also a letterhead design to function for the purposes of invoicing, all mail requirements, with header to be distinctive while the footer ties page together and incorporates all necessary information.

For now, please use generic / dummy text and when a winner is selected, I will disclose the contact information.

Hi Designers! Please read the updated brief which includes the design of a business card and letterhead. Thank you!

```html
<!DOCTYPE html>
<html lang="en">
<head>
<meta charset="utf-8">
<title>VKM Ltd – Business Card</title>
<link href="https://fonts.googleapis.com/css2?family=Playfair+Display:wght@700&family=Roboto:wght@400;500;700&display=swap" rel="stylesheet">
<style>
  :root{
    --bg:#1e1e1f;
    --card:#ffffff;
    --royal:#1a3aa0;
    --royal-deep:#12308f;
    --gold:#c9a227;
    --ink:#1d2b6e;
    --muted:#3a4266;
  }
  *{box-sizing:border-box;margin:0;padding:0}
  html,body{width:1200px;height:899px;overflow:hidden;background:var(--bg)}
  body{font-family:"Roboto",Arial,sans-serif;position:relative}
  .card{position:absolute;top:300px;width:540px;height:300px;overflow:hidden;box-shadow:0 10px 30px rgba(0,0,0,.45)}
  .card--front{left:50px;background:var(--card)}
  .card--back{left:610px;background:var(--royal)}

  .brand{position:absolute;left:34px;top:40px;display:flex;align-items:center;gap:12px}
  .brand__dot{width:18px;height:18px;border-radius:50%;background:var(--gold)}
  .brand__name{font-family:"Playfair Display",Georgia,serif;font-weight:700;font-size:50px;color:var(--royal-deep);letter-spacing:1px;line-height:1}

  .rule{position:absolute;height:1.5px;background:var(--royal)}
  .rule--top{left:250px;right:26px;top:118px}
  .rule--mid{left:34px;right:26px;top:230px}

  .person{position:absolute;left:34px;top:124px}
  .person__name{font-size:20px;font-weight:700;color:var(--gold)}
  .person__role{font-size:13px;color:var(--muted);margin-top:2px}

  .contacts{position:absolute;left:34px;top:178px;right:26px;display:grid;grid-template-columns:auto auto;column-gap:26px;row-gap:8px;justify-content:start}
  .contact{display:flex;align-items:center;gap:8px;font-size:14px;line-height:16px;color:var(--ink)}
  .contact svg{width:13px;height:13px;flex:none}

  .address{position:absolute;left:34px;top:240px;font-size:14px;color:var(--ink)}

  .band{position:absolute;left:0;right:0;bottom:0;height:16px;background:var(--royal)}
  .band__accent{position:absolute;left:0;bottom:0;width:32px;height:16px;background:var(--gold)}

  .pattern{position:absolute;inset:0;background:linear-gradient(120deg,#1a349a 0%,#1b3cae 55%,#2148c0 100%)}
  .back__mark{position:absolute;right:56px;top:120px;width:26px;height:26px;border-radius:50%;background:var(--gold)}
</style>
</head>
<body>
  <section class="card card--front" aria-label="Business card front">
    <div class="brand">
      <span class="brand__name">VKM Ltd</span>
      <span class="brand__dot"></span>
    </div>
    <div class="rule rule--top"></div>
    <div class="person">
      <p class="person__name">Daniel Reed</p>
      <p class="person__role">Manager</p>
    </div>
    <div class="contacts">
      <p class="contact">
        <svg viewBox="0 0 16 16" fill="var(--gold)"><path d="M3.6 1.5l2.3 2.3-1.3 1.9c.9 2 2.6 3.7 4.6 4.6l1.9-1.3 2.3 2.3-1.4 2.2C7.2 13.3 2.7 8.8 1.5 3z"/></svg>
        555-010-2468
      </p>
      <p class="contact">
        <svg viewBox="0 0 16 16" fill="none" stroke="var(--gold)" stroke-width="1.6"><circle cx="8" cy="8" r="6.5"/><path d="M1.5 8h13M8 1.5c2.4 2.6 2.4 10.4 0 13M8 1.5c-2.4 2.6-2.4 10.4 0 13"/></svg>
        www.yourwebsite.com
      </p>
      <p class="contact">
        <svg viewBox="0 0 16 16" fill="none" stroke="var(--gold)" stroke-width="1.6"><rect x="1.5" y="3.5" width="13" height="9" rx="1"/><path d="M1.5 4l6.5 5 6.5-5"/></svg>
        youremail@mailbox.com
      </p>
    </div>
    <div class="rule rule--mid"></div>
    <p class="address">Your address, city state, ZIP 0000</p>
    <div class="band"><div class="band__accent"></div></div>
  </section>

  <section class="card card--back" aria-label="Business card back">
    <div class="pattern" role="img" aria-label="Tone-on-tone repeating floral pattern in royal blue"></div>
    <div class="back__mark"></div>
  </section>
</body>
</html>
```